bird wings, breathing, coaching, rhythm, heart

I would like this card design to be inspired by the following Rumi poem - now that I see some cards with the poem on it, I am pretty sure I don't want that. The feel of the cards should be watery and emotional, one of rhythm, breathing like a pendulum. An Ouroboros, (alchemical imagery in general), Birds, lungs, bird wings, hands, clouds, water, waves and rivers are all good images. Simple elegance is appreciated.
Cards should contain my name, title (coach), address, phone number and email address.
Your grief for what you've lost lifts a mirror
up to where you're bravely working.
Expecting the worst, you look, and instead,
here's the joyful face you've been wanting to see.
Your hand opens and closes and opens and closes.
If it were always a fist or always stretched open,
you would be paralyzed.
Your deepest presence
is in every small contracting and expanding,
the two as beautifully balanced and coordinated
as birdwings.
Contact Information for Business Card
Dorran Pelkwith, MA
Coach
4718 Varno St.
Berkeley, CA 94188
415-382-6649
pelkwith@mailvaro.net
Designer to choose colors to be used in the design.

```html
<!DOCTYPE html>
<html lang="en">
<head>
<meta charset="utf-8">
<title>Dorran Pelkwith, MA — Coach — Business Card</title>
<link rel="stylesheet" href="https://fonts.googleapis.com/css2?family=Lato:wght@400&display=swap">
<style>
  :root {
    --backdrop: #2b2b2b;
    --card-teal: #0d9296;
    --band-teal: #078a8e;
    --mark-light: #6fcfca;
    --name-yellow: #f2dc1f;
    --text-light: #eef7f6;
    --rule: rgba(190, 235, 232, 0.45);
  }
  * { margin: 0; padding: 0; box-sizing: border-box; }
  html, body {
    width: 1200px;
    height: 1200px;
    overflow: hidden;
    background: var(--backdrop);
  }
  .canvas {
    position: relative;
    width: 1200px;
    height: 1200px;
  }
  .card {
    position: absolute;
    top: 310px;
    width: 364px;
    height: 594px;
    background: var(--card-teal);
    box-shadow: 0 4px 10px rgba(0, 0, 0, 0.55);
    overflow: hidden;
  }
  .card--front { left: 234px; }
  .card--back { left: 627px; width: 369px; }

  .contact-band {
    position: absolute;
    left: 0;
    top: 170px;
    width: 100%;
    height: 252px;
    background: var(--band-teal);
    display: flex;
    flex-direction: column;
    align-items: center;
    font-family: "Lato", sans-serif;
    color: var(--text-light);
    text-align: center;
  }
  .contact-band__name {
    margin-top: 19px;
    font-size: 23px;
    line-height: 28px;
    color: var(--name-yellow);
    font-weight: 400;
    white-space: nowrap;
  }
  .contact-band__title {
    margin-top: 3px;
    font-size: 17px;
    line-height: 22px;
  }
  .contact-band__rule {
    width: 172px;
    height: 1px;
    background: var(--rule);
    border: 0;
  }
  .contact-band__rule--upper { margin-top: 18px; }
  .contact-band__rule--lower { margin-top: 15px; }
  .contact-band__line {
    font-size: 17px;
    line-height: 22px;
    white-space: nowrap;
  }
  .contact-band__phone { margin-top: 18px; }
  .contact-band__street { margin-top: 21px; }

  .emblem-area {
    position: absolute;
    left: 14px;
    top: 115px;
    width: 340px;
    height: 362px;
    border-radius: 50%;
    background: radial-gradient(circle at 50% 50%,
      rgba(111, 207, 202, 0) 0%,
      rgba(111, 207, 202, 0) 52%,
      rgba(111, 207, 202, 0.55) 70%,
      rgba(111, 207, 202, 0.2) 84%,
      rgba(111, 207, 202, 0) 100%);
  }
</style>
</head>
<body>
<main class="canvas">
  <section class="card card--front" aria-label="Business card front">
    <div class="contact-band">
      <h1 class="contact-band__name">DORRAN PELKWITH, MA</h1>
      <p class="contact-band__title">Coach</p>
      <hr class="contact-band__rule contact-band__rule--upper">
      <p class="contact-band__line contact-band__phone">415-382-6649</p>
      <p class="contact-band__line">pelkwith@mailvaro.net</p>
      <hr class="contact-band__rule contact-band__rule--lower">
      <p class="contact-band__line contact-band__street">4718 Varno St.</p>
      <p class="contact-band__line">Berkeley, CA 94188</p>
    </div>
  </section>

  <section class="card card--back" aria-label="Business card back">
    <div class="emblem-area" role="img" aria-label="Place for a round pale teal emblem illustration"></div>
  </section>
</main>
</body>
</html>
```